Hi Designers,

I will need 4 web pages designed. The web page looks like an App (if you click on the logo, or the icon on an iPad, it will take you to the website), but it is still a webpage.

Please check the attachment on this brief to understand what specific pages I need to be designed.

A .PSD (straight-up PhotoShop image) as final deliverable is fine, as long as you give us the exact “web color numbers”.

The design is for desktop and iPad but in a single unified web application, NOT separate web app and (native) iPad app.

Details:

Brightwater Policy Partners is developing a browser-based application for use on any mobile device or desktop. The app will be used by corporations to communicate with their employees regarding legal, regulatory and company requirements for conducting business. The app is known as “Harbor Guidance Portal.” When the user clicks on the icon for Harbor Guidance Portal, they will enter a site full of information that a company deems necessary for the employee to do his/her job. There are several content sections within the site, including a login page, training, policies, forms, news feeds and blogs.

The application has been built using Microsoft .NET, and fully supports CSS-type skinning; it uses traditional page layouts. We are seeking a product logo concept (image), a master application/desktop icon (image), as well as a full color scheme/theme/skin design for all areas of the application (header area, body text, menu bar, etc.) in the form of a CSS. The look should be clean, crisp and professional; nothing cartoony or whimsical. It should be easy to read and “airy”.

We have sketched prototypes for the basic application page layout that we can send as a next step of the process.
Updates

Screen shots have been uploaded to this project.  Please use them to guide your design.

Dear designers,

I apologize for the delay in providing feedback. My partners and I will provide feedback in a few days. Thank you for your patience.

Industry/Entity Type

Business

Font styles to use
Other font styles liked:
• see font on screen shots when uploaded

```html
<!DOCTYPE html>
<html lang="en">
<head>
<meta charset="utf-8">
<title>Harbor Guidance Portal – Login</title>
<link href="https://fonts.googleapis.com/css2?family=Open+Sans:wght@400;600;700&family=Arimo:wght@400&display=swap" rel="stylesheet">
<style>
  :root {
    --bg-light: #58737c;
    --bg-mid: #47596c;
    --bg-dark: #2f3c61;
    --panel: #042a50;
    --field: #03203f;
    --field-border: #8797ab;
    --text: #ffffff;
    --icon: #d9dde2;
    --accent-top: #ff9040;
    --accent-bottom: #f45c12;
    --footer: #04284d;
    --mark: #e07a1c;
  }
  * { box-sizing: border-box; margin: 0; padding: 0; }
  html, body { width: 1200px; height: 800px; overflow: hidden; }
  body {
    position: relative;
    font-family: "Open Sans", sans-serif;
    color: var(--text);
    background:
      radial-gradient(ellipse 620px 520px at 380px 420px, var(--bg-light) 0%, var(--bg-mid) 55%, transparent 100%),
      linear-gradient(90deg, var(--bg-mid) 0%, #3d4e69 55%, var(--bg-dark) 100%);
  }
  .brand-badge {
    position: absolute; left: 482px; top: 84px; width: 196px; height: 61px;
    background: var(--panel);
    box-shadow: 0 1px 4px rgba(0,0,0,.35);
    display: flex; align-items: center; gap: 14px; padding-left: 22px;
  }
  .brand-dot { width: 26px; height: 26px; border-radius: 50%; background: #2fa7d6; }
  .brand-name { font-size: 19px; font-weight: 600; letter-spacing: .2px; }
  .login-panel {
    position: absolute; left: 282px; top: 180px; width: 634px; height: 392px;
    background: var(--panel);
    box-shadow: 0 1px 5px rgba(0,0,0,.35);
  }
  .login-title {
    position: absolute; top: 24px; width: 100%; text-align: center;
    font-size: 38px; font-weight: 400;
  }
  .field-icon { position: absolute; left: 80px; width: 34px; height: 34px; }
  .field-icon.user { top: 113px; }
  .field-icon.key { top: 202px; }
  .field {
    position: absolute; left: 136px; width: 378px; height: 61px;
    background: var(--field);
    border: 1px solid var(--field-border); border-radius: 4px;
    display: flex; align-items: center; padding-left: 29px;
    font-size: 18px;
  }
  .field.username { top: 104px; }
  .field.password { top: 187px; }
  .dots { font-size: 14px; letter-spacing: 1.6px; }
  .caret { display: inline-block; width: 1px; height: 24px; background: var(--text); margin-left: 4px; }
  .login-button {
    position: absolute; left: 368px; top: 267px; width: 147px; height: 46px;
    background: linear-gradient(var(--accent-top), var(--accent-bottom));
    border: 1px solid #ffa35c; border-radius: 2px;
    color: var(--text); font: 700 21px "Open Sans", sans-serif;
  }
  .forgot-link {
    position: absolute; right: 120px; top: 331px;
    font-size: 10.5px; color: var(--text); text-decoration: none;
  }
  .portal-mark {
    position: absolute; left: 534px; top: 606px; width: 52px; height: 52px;
    border-radius: 50%; background: var(--mark);
  }
  .portal-name {
    position: absolute; left: 0; top: 676px; width: 1160px; text-align: center;
    font: 400 19px "Arimo", sans-serif; color: var(--text);
    text-shadow: 0 1px 2px rgba(0,0,0,.4);
  }
  .site-footer {
    position: absolute; left: 0; bottom: 0; width: 1200px; height: 50px;
    background: var(--footer);
    display: flex; align-items: center; justify-content: center;
    font: 400 11px "Arimo", sans-serif;
  }
</style>
</head>
<body>
  <div class="brand-badge">
    <span class="brand-dot"></span>
    <span class="brand-name">Quorvane</span>
  </div>

  <main class="login-panel">
    <h1 class="login-title">Login</h1>

    <svg class="field-icon user" viewBox="0 0 34 34" aria-hidden="true">
      <ellipse cx="17" cy="10" rx="6" ry="8" fill="var(--icon)"/>
      <path d="M2 32 C3 23 9 21 13 19 L21 19 C25 21 31 23 32 32 Z" fill="var(--icon)"/>
    </svg>
    <div class="field username">Username</div>

    <svg class="field-icon key" viewBox="0 0 34 34" aria-hidden="true">
      <circle cx="10" cy="10" r="7.5" fill="var(--icon)"/>
      <circle cx="8" cy="8" r="2" fill="var(--panel)"/>
      <path d="M14 14 L28 28 L26 30 L24 28 L23 29 L21 27 L22 26 L12 16 Z" fill="var(--icon)"/>
    </svg>
    <div class="field password"><span class="dots">●●●●●●●●●●</span><span class="caret"></span></div>

    <button class="login-button">Login</button>
    <a class="forgot-link" href="#">Fotgot Password ?</a>
  </main>

  <span class="portal-mark"></span>
  <div class="portal-name">Harbor Guidance Portal</div>

  <footer class="site-footer">Content copyright 2013. HGP. All rights reserved.</footer>
</body>
</html>
```